Brightway Carpet and Tile cleaning Business card Design

I need a design that has the same feel as my van.
i would also like a prominent "Review us on facebook" somewhere, but not that it makes it look silly.
I would like the card to have a little bit of grey or black in the design as well.

It will need contact details
phone: 0455 817264
email: rkbrightwayclean@mailbox-example.com
website: www.brightwaycarpetandtilecleaning-example.com.au
facebook: /brightwaycarpetandtilecleaning

Industry/Entity Type

Business

Contact Information for Business Card

Phone number 0455817264
Email rkbrightwayclean@mailbox-example.com
Website www.brightwaycarpetandtilecleaning-example.com.au
Facebook/brightwaycarpetandtilecleaning

Colors
000000

Requirements
Must have
• Same feel as my van
• I want the card to stand out from the crowd
Nice to have
• Maybe include a tiny bit of a third colour? Grey's,blacks, orange?

```html
<!DOCTYPE html>
<html lang="en">
<head>
<meta charset="utf-8">
<title>Brightway Carpet and Tile cleaning – Business Card</title>
<link href="https://fonts.googleapis.com/css2?family=Roboto:wght@400;500;700&display=swap" rel="stylesheet">
<style>
  :root {
    --black: #000000;
    --white: #ffffff;
    --green: #7dc242;
    --blue: #1fa9dc;
    --grey: #6d6e71;
    --ink: #111111;
    --stage: #ece9e4;
  }
  * { box-sizing: border-box; margin: 0; padding: 0; }
  html, body {
    width: 1189px; height: 1200px; overflow: hidden;
    background: var(--stage);
    font-family: "Roboto", Arial, sans-serif;
  }
  .canvas { position: relative; width: 1189px; height: 1200px; }
  .card {
    position: absolute; width: 860px; height: 490px; overflow: hidden;
    background: var(--black);
    box-shadow: 0 8px 24px rgba(0,0,0,.25);
  }
  .card-front { left: 230px; top: 70px; }
  .card-back { left: 100px; top: 640px; }
  .card-art { position: absolute; inset: 0; width: 100%; height: 100%; }

  .brand {
    position: absolute; display: flex; flex-direction: column; align-items: flex-end;
  }
  .brand-row { display: flex; align-items: center; gap: 12px; }
  .brand-dot { width: 22px; height: 22px; border-radius: 50%; background: var(--blue); }
  .brand-name { font-weight: 700; font-size: 64px; line-height: 1; color: var(--blue); letter-spacing: -1px; }
  .brand-tagline { font-size: 19px; letter-spacing: 3px; color: var(--grey); margin-top: 4px; }

  .card-front .brand { right: 70px; top: 120px; }

  .person { position: absolute; right: 40px; top: 246px; text-align: right; }
  .person-name { font-weight: 700; font-size: 28px; color: var(--ink); }
  .person-role { font-size: 21px; color: var(--green); }

  .contacts { position: absolute; right: 40px; top: 322px; list-style: none; text-align: right; }
  .contact {
    display: flex; justify-content: flex-end; align-items: center; gap: 8px;
    font-size: 20px; color: var(--ink); height: 30px;
  }
  .contact-icon { width: 22px; height: 22px; background: var(--green); display: block; }

  .card-back .brand { right: 80px; top: 160px; }
  .services { position: absolute; right: 42px; top: 300px; width: 560px; }
  .services-title { text-align: right; font-weight: 700; font-size: 23px; color: var(--ink); margin-bottom: 14px; }
  .services-cols { display: flex; justify-content: flex-end; gap: 36px; }
  .services-list { list-style: none; }
  .service {
    display: flex; justify-content: flex-end; align-items: center; gap: 14px;
    font-size: 19px; color: var(--ink); height: 28px;
  }
  .service::after { content: ""; width: 8px; height: 8px; border-radius: 50%; background: var(--blue); }
  .services-web { text-align: right; font-size: 21px; color: var(--ink); margin-top: 10px; }
</style>
</head>
<body>
<main class="canvas">

  <section class="card card-front">
    <svg class="card-art" viewBox="0 0 935 533" preserveAspectRatio="none">
      <rect width="935" height="533" fill="var(--black)"/>
      <ellipse cx="600" cy="100" rx="542" ry="472" fill="var(--white)"/>
      <ellipse cx="600" cy="100" rx="536" ry="466" fill="var(--green)"/>
      <ellipse cx="600" cy="100" rx="522" ry="452" fill="var(--white)"/>
    </svg>
    <div class="brand">
      <div class="brand-row"><span class="brand-dot"></span><span class="brand-name">Brightway</span></div>
      <div class="brand-tagline">CARPET &amp; TILE CLEANING</div>
    </div>
    <div class="person">
      <p class="person-name">Robert Keane</p>
      <p class="person-role">Managing/Director</p>
    </div>
    <ul class="contacts">
      <li class="contact">0455 817264
        <svg class="contact-icon" viewBox="0 0 22 22"><rect width="22" height="22" fill="var(--green)"/><path d="M5 9c0-3 12-3 12 0v2h-3V9H8v2H5z M7 12h8l1 5H6z" fill="var(--white)"/></svg></li>
      <li class="contact">rkbrightwayclean@mailbox-example.com
        <svg class="contact-icon" viewBox="0 0 22 22"><rect width="22" height="22" fill="var(--green)"/><rect x="4" y="6" width="14" height="10" fill="none" stroke="var(--white)" stroke-width="1.5"/><path d="M4 6l7 6 7-6" fill="none" stroke="var(--white)" stroke-width="1.5"/></svg></li>
      <li class="contact">www.brightwaycarpetandtilecleaning-example.com.au
        <svg class="contact-icon" viewBox="0 0 22 22"><rect width="22" height="22" fill="var(--green)"/><circle cx="11" cy="11" r="6.5" fill="none" stroke="var(--white)" stroke-width="1.4"/><ellipse cx="11" cy="11" rx="3" ry="6.5" fill="none" stroke="var(--white)" stroke-width="1.2"/><path d="M4.5 11h13" stroke="var(--white)" stroke-width="1.2"/></svg></li>
      <li class="contact">/brightwaycarpetandtilecleaning <span class="contact-icon"></span></li>
    </ul>
  </section>

  <section class="card card-back">
    <svg class="card-art" viewBox="0 0 935 533" preserveAspectRatio="none">
      <defs>
        <linearGradient id="scene-tone" x1="0" y1="0" x2="1" y2="1">
          <stop offset="0" stop-color="#c9d3c4"/>
          <stop offset=".5" stop-color="#e4e8e1"/>
          <stop offset="1" stop-color="#d7dad4"/>
        </linearGradient>
      </defs>
      <rect width="935" height="533" fill="var(--black)"/>
      <ellipse cx="660" cy="580" rx="600" ry="582" fill="var(--white)"/>
      <ellipse cx="660" cy="580" rx="594" ry="576" fill="var(--green)"/>
      <ellipse cx="660" cy="580" rx="580" ry="562" fill="var(--white)"/>
      <ellipse cx="660" cy="580" rx="574" ry="556" fill="url(#scene-tone)" role="img" aria-label="Faded photo of a cleaning wand on a window in front of garden greenery"/>
    </svg>
    <div class="brand">
      <div class="brand-row"><span class="brand-dot"></span><span class="brand-name">Brightway</span></div>
      <div class="brand-tagline">CARPET &amp; TILE CLEANING</div>
    </div>
    <div class="services">
      <h2 class="services-title">OUR SERVICES</h2>
      <div class="services-cols">
        <ul class="services-list">
          <li class="service">Pet Damage Repair</li>
          <li class="service">Flood Damage Repair</li>
          <li class="service">Carpet Repair</li>
        </ul>
        <ul class="services-list">
          <li class="service">Carpet Cleaning</li>
          <li class="service">Tile and Grout Cleaning</li>
          <li class="service">Upholstery Cleaning</li>
        </ul>
      </div>
      <p class="services-web">www.brightwaycarpetandtilecleaning-example.com.au</p>
    </div>
  </section>

</main>
</body>
</html>
```